Brightwater Kidney Services Brochure - Marketing brochure for a dialysis company in the USA

I want a brochure to be created for my business. I have a brochure that can be used as a comparison. My old Company name is Gulf Plains Renal Infusions. The new Company Name is Brightwater Kidney Services. I have a sample of the Old Brochure. and I uploaded the Logo of BKS. It will be used by my sales agents to introduce my company to potential client hospitals.

Target Market(s)

CEOs of Acute Hospitals and Medical Centers

Industry/Entity Type

Health Care

Requirements
Must have
• Use the sample as a guide. This project is for a 4 page brochure. (2 letter size pages folded in half crosswise) Use the text from the old brochure to the new brochure, replacing the old info with the new company info as needed.
Nice to have
• Here is my company info:
• Brightwater Kidney Services
• 4185 W 61st Ave
• Suite F
• It will be nice if the designer can give me the project files that would allow me to edit the text of the brochure.
• McAllen, TX 78516
• (956) 417-2608
• admin@BrightwaterKidneyLLC.example
• www.brightwaterkidney.example

```html
<!DOCTYPE html>
<html lang="en">
<head>
<meta charset="utf-8">
<title>Brightwater Kidney Services Brochure</title>
<link href="https://fonts.googleapis.com/css2?family=Libre+Baskerville:wght@700&family=Open+Sans:wght@400;600;700;800&display=swap" rel="stylesheet">
<style>
:root{
  --red:#d2232a;
  --red-dark:#9e1b20;
  --blue:#1c3f94;
  --blue-dark:#12295f;
  --ink:#333a44;
  --paper:#ffffff;
  --backdrop:#e6e4e1;
  --photo-a:#9fb6c9;
  --photo-b:#dfe7ee;
}
*{box-sizing:border-box;margin:0;padding:0}
html,body{width:1200px;height:2484px;overflow:hidden}
body{background:var(--backdrop);font-family:"Open Sans",sans-serif;color:var(--ink);position:relative}
.spread{position:absolute;left:50px;width:1100px;height:580px;background:var(--paper);box-shadow:0 4px 14px rgba(0,0,0,.18);overflow:hidden}
.spread--cover{top:20px}
.spread--why{top:641px}
.spread--different{top:1262px}
.spread--growth{top:1883px}
.page{position:absolute;top:0;width:550px;height:580px}
.page--left{left:0}
.page--right{left:550px}
.fold{position:absolute;left:549px;top:0;width:2px;height:580px;background:linear-gradient(90deg,rgba(0,0,0,.06),rgba(0,0,0,0))}
.band-top{position:absolute;left:0;top:0;width:1100px;height:80px}
.band-foot{position:absolute;left:0;bottom:0;width:100%;height:34px;background:var(--blue);border-top:6px solid var(--red)}
.photo{position:absolute;background:linear-gradient(135deg,var(--photo-a),var(--photo-b));border:3px solid #fff;box-shadow:0 1px 4px rgba(0,0,0,.25)}
.photo--round{border-radius:50%}
.brand{position:absolute;display:flex;align-items:center;gap:8px}
.brand__mark{width:18px;height:18px;background:var(--red)}
.brand__name{font-family:"Open Sans",sans-serif;font-weight:800;color:var(--blue);font-size:34px;letter-spacing:1px;line-height:1}
.brand--tab{background:#fff;padding:8px 16px;box-shadow:0 1px 4px rgba(0,0,0,.2)}
.text{position:absolute;font-size:11.5px;line-height:1.55}
.text p{margin-bottom:8px}
.text h3{font-size:12px;font-weight:700;color:var(--blue);margin:4px 0 5px;line-height:1.35}
.heading-about{position:absolute;left:40px;top:40px;font-family:"Libre Baskerville",serif;color:var(--red);font-size:24px}
.contact{position:absolute;left:40px;top:380px;display:flex;align-items:center;gap:22px}
.contact__lines{font-size:13px;line-height:1.6}
.contact__phone{font-weight:800;color:var(--red);font-size:18px}
.cover-title{position:absolute;left:190px;top:364px;width:330px;font-family:"Libre Baskerville",serif;color:var(--red-dark);font-size:18px;line-height:1.3;text-transform:uppercase}
.cover-call{position:absolute;left:0;top:462px;width:550px;height:56px;background:var(--red);color:#fff;font-weight:800;font-size:28px;letter-spacing:2px;display:flex;align-items:center;justify-content:center}
.icon-phone{display:inline-block;vertical-align:middle;margin-right:4px}
</style>
</head>
<body>

<section class="spread spread--cover">
  <div class="page page--left">
    <h2 class="heading-about">ABOUT US</h2>
    <div class="text" style="left:40px;top:86px;width:470px;font-size:12.5px">
      <p>Brightwater Kidney Services is a full-service acute dialysis provider serving hospitals across South Texas. We deliver hemodialysis and related therapies at the bedside, around the clock.</p>
      <p>Our team of experienced nurses and technicians works alongside your physicians to give every patient safe, timely and consistent care.</p>
      <p>Partnering with us removes the cost of staff, equipment and training from your budget while keeping quality high.</p>
      <p>Visit us at 4185 W 61st Ave, Suite F, McAllen, TX 78516.</p>
    </div>
    <div class="contact">
      <div class="brand" style="position:static"><span class="brand__mark"></span><span class="brand__name">BKS</span></div>
      <div class="contact__lines">
        <div class="contact__phone">
          <svg class="icon-phone" width="16" height="16" viewBox="0 0 24 24"><path fill="#d2232a" d="M6.6 10.8a15 15 0 0 0 6.6 6.6l2.2-2.2c.3-.3.7-.4 1-.2 1.1.4 2.3.6 3.6.6.6 0 1 .4 1 1V20c0 .6-.4 1-1 1A17 17 0 0 1 3 4c0-.6.4-1 1-1h3.5c.6 0 1 .4 1 1 0 1.3.2 2.5.6 3.6.1.3 0 .7-.2 1z"/></svg>(956) 417-2608
        </div>
        <div>www.brightwaterkidney.example</div>
        <div>admin@BrightwaterKidneyLLC.example</div>
      </div>
    </div>
    <div class="band-foot"></div>
  </div>

  <div class="page page--right">
    <div class="photo" role="img" aria-label="Patient receiving dialysis in a hospital room with a nurse beside the machine" style="left:40px;top:66px;width:470px;height:270px;border-radius:0 0 60px 60px"></div>
    <svg class="band-top" style="width:550px" viewBox="0 0 550 80" preserveAspectRatio="none">
      <path d="M0 0H550V30C420 52 200 20 0 44Z" fill="#d2232a"/>
      <path d="M0 50C200 26 420 58 550 36" stroke="#1c3f94" stroke-width="5" fill="none"/>
    </svg>
    <div class="brand brand--tab" style="right:24px;top:0"><span class="brand__mark"></span><span class="brand__name" style="font-size:26px">BKS</span></div>
    <div class="brand" style="left:36px;top:372px"><span class="brand__mark"></span><span class="brand__name">BKS</span></div>
    <h1 class="cover-title">Tired of paying outrageous prices for inpatient dialysis</h1>
    <div class="cover-call">CALL US NOW</div>
    <div class="band-foot"></div>
  </div>
  <div class="fold"></div>
</section>

<section class="spread spread--why">
  <svg class="band-top" viewBox="0 0 1100 80" preserveAspectRatio="none">
    <path d="M0 0H1100V18C850 40 700 8 550 30C380 52 200 10 0 36Z" fill="#d2232a"/>
    <path d="M0 44C200 18 380 60 550 38C700 16 850 48 1100 26" stroke="#1c3f94" stroke-width="4" fill="none"/>
  </svg>
  <div class="page page--left">
    <div class="photo" role="img" aria-label="Nurse preparing a dialysis machine" style="left:40px;top:66px;width:110px;height:110px"></div>
    <div class="text" style="left:168px;top:66px;width:340px">
      <h3>Why is Brightwater Kidney Services (BKS) the preferred provider in the area?</h3>
      <p>BKS has served acute hospitals in the region for years, providing dependable dialysis teams whenever and wherever they are needed.</p>
    </div>
    <div class="text" style="left:40px;top:196px;width:300px">
      <h3>Our facility provides inpatient care with modern, reliable equipment.</h3>
      <p>Each unit is maintained and tested on a strict schedule so treatments begin on time and run without interruption.</p>
      <p>Portable water systems let us treat patients in any room, including intensive care and step-down units.</p>
      <h3>What type of facilities operate with BKS?</h3>
      <p>Short-term acute hospitals, long-term care centers and rehabilitation units all rely on our services for their patients.</p>
      <p>We adapt our workflow to each hospital's policies and charting system.</p>
    </div>
    <div class="photo" role="img" aria-label="Dialysis machine at a bedside" style="left:360px;top:210px;width:150px;height:200px"></div>
    <div class="band-foot"></div>
  </div>
  <div class="page page--right">
    <div class="brand" style="left:232px;top:54px"><span class="brand__mark"></span><span class="brand__name" style="font-size:28px">BKS</span></div>
    <div class="text" style="left:30px;top:100px;width:230px">
      <p>Our staff is available seven days a week, including holidays, and can respond within hours of a request.</p>
      <p>Every nurse holds national certification and completes yearly training in infection control and patient safety.</p>
    </div>
    <div class="photo" role="img" aria-label="Care team reviewing a patient chart" style="left:30px;top:250px;width:230px;height:140px"></div>
    <div class="text" style="left:30px;top:405px;width:230px">
      <p>A single call to our office schedules a treatment, day or night.</p>
    </div>
    <div class="text" style="left:285px;top:100px;width:235px">
      <p>We handle all water treatment, supplies and documentation, letting your team focus on the patient.</p>
      <h3>How can BKS help my bottom line?</h3>
      <p>Outsourcing dialysis lowers fixed costs and converts them into a clear, predictable rate per treatment.</p>
      <p>You avoid buying machines, hiring specialist staff and paying for overtime when census rises.</p>
      <h3>Do you offer a trial period?</h3>
      <p>Yes. New partners can begin with a short agreement to review our service before signing a longer contract.</p>
    </div>
    <div class="band-foot"></div>
  </div>
  <div class="fold"></div>
</section>

<section class="spread spread--different">
  <svg class="band-top" viewBox="0 0 1100 80" preserveAspectRatio="none">
    <path d="M0 0H1100V18C850 40 700 8 550 30C380 52 200 10 0 36Z" fill="#d2232a"/>
    <path d="M0 44C200 18 380 60 550 38C700 16 850 48 1100 26" stroke="#1c3f94" stroke-width="4" fill="none"/>
  </svg>
  <div class="page page--left">
    <div class="photo" role="img" aria-label="Hospital corridor with dialysis equipment" style="left:40px;top:66px;width:120px;height:100px"></div>
    <div class="text" style="left:178px;top:66px;width:330px">
      <h3>How is Brightwater Kidney Services different from its competitors?</h3>
      <p>We combine local ownership with strict clinical standards, giving hospitals a partner who answers the phone and knows their floors.</p>
    </div>
    <div class="text" style="left:40px;top:196px;width:250px">
      <p>Our pricing is transparent, with no hidden fees for supplies, travel or after-hours calls.</p>
      <p>Every hospital has a named clinical manager who reviews quality reports each month.</p>
      <p>We track treatment times, outcomes and patient feedback and share the results openly.</p>
      <p>Our nurses live in the community they serve, so response times stay short.</p>
    </div>
    <div class="photo" role="img" aria-label="Nurse connecting a patient to a dialysis line" style="left:310px;top:196px;width:200px;height:210px"></div>
    <div class="band-foot"></div>
  </div>
  <div class="page page--right">
    <div class="brand" style="left:232px;top:54px"><span class="brand__mark"></span><span class="brand__name" style="font-size:28px">BKS</span></div>
    <div class="text" style="left:30px;top:100px;width:235px">
      <h3>How does an acute inpatient dialysis contract work?</h3>
      <p>A simple agreement sets the services, response times and rate. We supply staff and equipment; you supply the room.</p>
      <h3>What is CRRT?</h3>
      <p>Continuous renal replacement therapy gently filters blood over many hours for critically ill patients.</p>
      <p>Our CRRT nurses stay with the patient and work closely with your intensive care team.</p>
    </div>
    <div class="photo photo--round" role="img" aria-label="Close view of a dialysis filter" style="left:320px;top:100px;width:140px;height:140px"></div>
    <div class="text" style="left:285px;top:260px;width:235px">
      <h3>Does BKS offer other therapies?</h3>
      <p>Yes. We also provide plasmapheresis and slow low-efficiency dialysis on request.</p>
      <p>Each therapy follows written protocols approved by your medical staff.</p>
    </div>
    <div class="band-foot"></div>
  </div>
  <div class="fold"></div>
</section>

<section class="spread spread--growth">
  <svg class="band-top" viewBox="0 0 1100 80" preserveAspectRatio="none">
    <path d="M0 0H1100V18C850 40 700 8 550 30C380 52 200 10 0 36Z" fill="#d2232a"/>
    <path d="M0 44C200 18 380 60 550 38C700 16 850 48 1100 26" stroke="#1c3f94" stroke-width="4" fill="none"/>
  </svg>
  <div class="page page--left">
    <div class="photo" role="img" aria-label="Nurse holding a patient's hand during treatment" style="left:40px;top:66px;width:130px;height:110px"></div>
    <div class="text" style="left:188px;top:66px;width:320px">
      <h3>Why will BKS grow in line with your hospital's needs?</h3>
      <p>As your census changes, we scale our staffing up or down so you never pay for idle capacity.</p>
    </div>
    <div class="text" style="left:40px;top:196px;width:470px">
      <h3>What are the qualifications of the BKS staff?</h3>
      <p>All nurses are registered, certified in nephrology and screened before their first shift.</p>
      <h3>How quickly can BKS start?</h3>
      <p>Most hospitals begin receiving treatments within two weeks of signing an agreement.</p>
      <h3>Who manages supplies and equipment?</h3>
      <p>We stock, clean and maintain every machine and keep a full log of service for your records.</p>
    </div>
    <div class="band-foot"></div>
  </div>
  <div class="page page--right">
    <div class="brand" style="left:232px;top:54px"><span class="brand__mark"></span><span class="brand__name" style="font-size:28px">BKS</span></div>
    <div class="text" style="left:30px;top:100px;width:490px">
      <h3>Is BKS accredited?</h3>
      <p>We meet all state and federal requirements and welcome audits from partner hospitals.</p>
    </div>
    <div class="photo" role="img" aria-label="Medical supplies prepared for dialysis" style="left:30px;top:190px;width:150px;height:120px"></div>
    <div class="text" style="left:200px;top:190px;width:320px">
      <h3>Who should I contact to learn more?</h3>
      <p>Call our office at (956) 417-2608 or email admin@BrightwaterKidneyLLC.example to arrange a visit with a sales representative.</p>
      <p>More details are at www.brightwaterkidney.example.</p>
    </div>
    <div class="band-foot"></div>
  </div>
  <div class="fold"></div>
</section>

</body>
</html>
```